Carpet cleaning company focused on high quality needs business cards

We are a growing company that just merged with another company and need to design a new business card. We do both residential as well as commercial cleaning. We do carpet, tile & grout, upholstery, hard floors, and stain & pet odor removal. We treat our customers like family and strive to achieve outstanding results with every job.

```html
<!DOCTYPE html>
<html lang="en">
<head>
<meta charset="utf-8">
<title>Rowan's Fresh Fiber Cleaning – Business Card</title>
<link rel="stylesheet" href="https://fonts.googleapis.com/css2?family=Bebas+Neue&family=Montserrat:wght@400;500;700;800&display=swap">
<style>
  :root {
    --backdrop: #3a3a3c;
    --card-white: #ffffff;
    --brand-blue: #1a7fc4;
    --brand-blue-deep: #0b64ab;
    --brand-blue-light: #3aa0e0;
    --brand-red: #ee3b36;
    --ink: #1d1d1f;
    --ink-soft: #3c3c3e;
    --rule: #9a9a9a;
  }
  * { box-sizing: border-box; margin: 0; padding: 0; }
  html, body { width: 1200px; height: 1200px; overflow: hidden; }
  body {
    background: var(--backdrop);
    font-family: "Montserrat", sans-serif;
    position: relative;
  }
  .card {
    position: absolute;
    left: 250px;
    width: 700px;
    height: 400px;
    border-radius: 36px;
    overflow: hidden;
  }
  /* ---------- Front ---------- */
  .card--front { top: 160px; background: var(--card-white); }
  .front-band { position: absolute; inset: 0; }
  .services {
    position: absolute; left: 48px; top: 118px;
  }
  .services__title {
    font-family: "Bebas Neue", sans-serif;
    font-size: 40px; letter-spacing: 0.5px;
    color: var(--brand-blue); line-height: 1; margin-bottom: 8px;
  }
  .services__list { list-style: none; }
  .services__item {
    display: flex; align-items: center; gap: 10px;
    font-family: "Bebas Neue", sans-serif;
    font-size: 28px; color: var(--ink); line-height: 1.2;
    padding-left: 22px;
  }
  .services__item svg { width: 20px; height: 20px; flex: none; }
  .divider {
    position: absolute; left: 352px; top: 70px;
    width: 1px; height: 160px; background: var(--rule);
  }
  .brand {
    position: absolute; left: 392px; top: 36px;
    display: flex; align-items: center; gap: 12px;
  }
  .brand__square { width: 46px; height: 46px; background: var(--brand-red); flex: none; }
  .brand__name {
    font-weight: 800; font-size: 19px; line-height: 1.1;
    color: var(--ink); text-transform: uppercase; width: 190px;
  }
  .contact { position: absolute; left: 392px; top: 118px; }
  .contact__name {
    font-weight: 500; font-size: 42px; color: var(--brand-blue);
    line-height: 1; letter-spacing: -0.5px;
  }
  .contact__title {
    font-size: 18px; color: var(--ink-soft); margin: 4px 0 14px 4px;
  }
  .contact__row {
    display: flex; align-items: center; gap: 10px;
    font-size: 17px; color: var(--ink); margin-bottom: 6px; padding-left: 14px;
  }
  .contact__row svg { width: 20px; height: 20px; flex: none; }
  .website {
    position: absolute; right: 34px; bottom: 38px;
    font-size: 16px; color: var(--card-white); letter-spacing: 0.3px;
    white-space: nowrap;
  }
  /* ---------- Back ---------- */
  .card--back {
    top: 620px;
    background: radial-gradient(circle at 48% 48%, var(--brand-blue-light) 0%, var(--brand-blue) 45%, var(--brand-blue-deep) 100%);
  }
  .back-lockup {
    position: absolute; inset: 0;
    display: flex; align-items: center; justify-content: center; gap: 30px;
  }
  .back-lockup__square { width: 170px; height: 170px; background: var(--brand-red); flex: none; }
  .back-lockup__name {
    font-weight: 800; font-size: 44px; line-height: 1.05;
    color: var(--card-white); text-transform: uppercase; width: 330px;
  }
</style>
</head>
<body>

  <section class="card card--front" aria-label="Business card front">
    <svg class="front-band" viewBox="0 0 700 400" aria-hidden="true">
      <path d="M0 358 H350 C378 358 392 350 406 338 L412 344 C398 358 382 366 352 366 H0 Z" fill="var(--brand-red)"/>
      <path d="M0 372 H360 C420 372 440 298 520 298 H700 V400 H0 Z" fill="var(--brand-blue)"/>
    </svg>

    <div class="services">
      <h2 class="services__title">Our Services</h2>
      <ul class="services__list">
        <li class="services__item"><svg viewBox="0 0 20 20"><circle cx="10" cy="10" r="8.5" fill="none" stroke="var(--brand-blue)" stroke-width="2"/><path d="M6 10.5 L9 13 L14.5 7" fill="none" stroke="var(--brand-blue)" stroke-width="2.2"/></svg>Carpet Cleaning</li>
        <li class="services__item"><svg viewBox="0 0 20 20"><circle cx="10" cy="10" r="8.5" fill="none" stroke="var(--brand-blue)" stroke-width="2"/><path d="M6 10.5 L9 13 L14.5 7" fill="none" stroke="var(--brand-blue)" stroke-width="2.2"/></svg>Upholstery Cleaning</li>
        <li class="services__item"><svg viewBox="0 0 20 20"><circle cx="10" cy="10" r="8.5" fill="none" stroke="var(--brand-blue)" stroke-width="2"/><path d="M6 10.5 L9 13 L14.5 7" fill="none" stroke="var(--brand-blue)" stroke-width="2.2"/></svg>Commercial Carpet Cleaning</li>
        <li class="services__item"><svg viewBox="0 0 20 20"><circle cx="10" cy="10" r="8.5" fill="none" stroke="var(--brand-blue)" stroke-width="2"/><path d="M6 10.5 L9 13 L14.5 7" fill="none" stroke="var(--brand-blue)" stroke-width="2.2"/></svg>Pet Odor Removal</li>
      </ul>
    </div>

    <div class="divider"></div>

    <div class="brand">
      <div class="brand__square"></div>
      <p class="brand__name">Rowan's Fresh Fiber Cleaning</p>
    </div>

    <div class="contact">
      <p class="contact__name">FULL NAME</p>
      <p class="contact__title">TITLE</p>
      <p class="contact__row"><svg viewBox="0 0 24 24"><path d="M6.6 10.8a15 15 0 0 0 6.6 6.6l2.2-2.2a1 1 0 0 1 1-.25 11.4 11.4 0 0 0 3.6.57 1 1 0 0 1 1 1V20a1 1 0 0 1-1 1A17 17 0 0 1 3 4a1 1 0 0 1 1-1h3.5a1 1 0 0 1 1 1c0 1.25.2 2.45.57 3.57a1 1 0 0 1-.25 1z" fill="var(--brand-blue)"/></svg>(555) 014-2290</p>
      <p class="contact__row"><svg viewBox="0 0 24 24"><rect x="2" y="5" width="20" height="14" fill="var(--brand-blue)"/><path d="M2 5 L12 13 L22 5 M2 19 L9 11 M22 19 L15 11" fill="none" stroke="var(--card-white)" stroke-width="1.6"/></svg>hello@rowanfreshfiber.com</p>
    </div>

    <p class="website">www.rowanfreshfiber.com</p>
  </section>

  <section class="card card--back" role="img" aria-label="Business card back: blue light-ray burst background with company name">
    <div class="back-lockup">
      <div class="back-lockup__square"></div>
      <p class="back-lockup__name">Rowan's Fresh Fiber Cleaning</p>
    </div>
  </section>

</body>
</html>
```